Business Card Design Project

We are Brightwell Staffing, a recruitment company based in London. We require a new business card design in order to present our business. We work in a number of areas recruiting professional in areas such as engineering and rail. Most of our work is based in the Middle East so our cards must have a universal, professional feel.

Visit our website: http://www.brightwell-staffing.example/ for more info

Industry/Entity Type

Business

Requirements
Must have
• Must be double sided

Must feature the companies logo on both sides of the card

Should incorporate the primary colours of the logo

Must be professional and contemporary, to fit in with the logo

Info: Name: Colin Marsh certRP MREC
Senior Recruitment Consultant
Address: 4 Orchard Mews Kelbrook London E94TQ
T: +44 (0)203 555 0147
M: +44 (0)7700 900 318
E: cmarsh@brightwell-staffing.example
W www.brightwell-staffing.example
Nice to have
• A modern style card

```html
<!DOCTYPE html>
<html lang="en">
<head>
<meta charset="utf-8">
<title>Brightwell Staffing – Business Card</title>
<link rel="stylesheet" href="https://fonts.googleapis.com/css2?family=Questrial&family=Open+Sans:wght@400;600;700&display=swap">
<style>
  :root {
    --page: #e9e9e9;
    --card-white: #f4f4f4;
    --grey-dark: #6e6e6e;
    --grey-mid: #8c8c8c;
    --grey-text: #7a7a7a;
    --green: #14936f;
    --white: #ffffff;
  }
  * { box-sizing: border-box; margin: 0; padding: 0; }
  html, body { width: 1200px; height: 900px; overflow: hidden; }
  body {
    background: var(--page);
    font-family: "Open Sans", Arial, sans-serif;
    position: relative;
  }
  .card {
    position: absolute;
    left: 290px;
    width: 620px;
    height: 360px;
    overflow: hidden;
    box-shadow: 0 8px 22px rgba(0,0,0,.18);
  }
  .card-back {
    top: 60px;
    background: linear-gradient(160deg, var(--grey-mid), var(--grey-dark));
    display: flex;
    align-items: center;
    justify-content: center;
  }
  .card-front { top: 480px; background: var(--card-white); }

  .brand { display: flex; align-items: center; gap: 12px; font-family: "Questrial", Arial, sans-serif; }
  .brand-dot { width: 34px; height: 34px; border-radius: 50%; }
  .brand-name { font-size: 38px; letter-spacing: -0.5px; line-height: 1; }
  .card-back .brand-dot { background: var(--white); }
  .card-back .brand-name { color: var(--white); }

  .card-front .brand { position: absolute; left: 34px; top: 150px; }
  .card-front .brand-dot { background: var(--green); }
  .card-front .brand-name { color: var(--grey-text); }

  .person { position: absolute; right: 30px; top: 44px; text-align: right; }
  .person-name { color: var(--green); font-weight: 700; font-size: 15px; }
  .person-title { color: var(--grey-text); font-size: 12px; margin-top: 2px; }
  .rule-top { position: absolute; left: 330px; right: 24px; top: 96px; height: 1px; background: var(--grey-text); }
  .address { position: absolute; right: 30px; top: 108px; text-align: right; color: var(--grey-text); font-size: 12.5px; line-height: 1.45; }
  .address-icon { position: absolute; right: -2px; top: -2px; }
  .address-lines { padding-right: 20px; }

  .rule-contact { position: absolute; left: 30px; width: 290px; top: 222px; height: 1px; background: var(--grey-text); }
  .contacts { position: absolute; left: 32px; top: 232px; list-style: none; }
  .contacts li { display: flex; align-items: center; gap: 10px; color: var(--grey-text); font-size: 14px; height: 20px; }
  .contact-icon { width: 13px; height: 13px; flex: none; }

  .swoosh { position: absolute; left: 0; top: 0; }
</style>
</head>
<body>
  <section class="card card-back" aria-label="Card back">
    <div class="brand">
      <span class="brand-dot"></span>
      <span class="brand-name">Brightwell Staffing</span>
    </div>
  </section>

  <section class="card card-front" aria-label="Card front">
    <svg class="swoosh" width="620" height="360" viewBox="0 0 620 360" aria-hidden="true">
      <path d="M0 360 C200 356 340 322 440 252 C510 204 570 196 620 200 L620 360 Z" fill="#7f7f7f"/>
      <path d="M0 350 C150 342 270 318 370 282" fill="none" stroke="var(--green)" stroke-width="4"/>
    </svg>

    <div class="person">
      <p class="person-name">Colin Marsh certRP MREC</p>
      <p class="person-title">Senior Recruitment Consultant</p>
    </div>
    <div class="rule-top"></div>
    <div class="address">
      <svg class="address-icon" width="13" height="13" viewBox="0 0 14 14" aria-hidden="true">
        <circle cx="7" cy="7" r="7" fill="var(--green)"/>
        <path d="M3.5 7.2 L7 4 L10.5 7.2 M4.8 6.6 V10 H9.2 V6.6" fill="none" stroke="#fff" stroke-width="1.2"/>
      </svg>
      <p class="address-lines">4 Orchard Mews Kelbrook London<br>E94TQ</p>
    </div>

    <div class="brand">
      <span class="brand-dot"></span>
      <span class="brand-name">Brightwell Staffing</span>
    </div>

    <div class="rule-contact"></div>
    <ul class="contacts">
      <li>
        <svg class="contact-icon" viewBox="0 0 14 14" aria-hidden="true"><circle cx="7" cy="7" r="7" fill="var(--green)"/><path d="M4.5 3.8 C4 6.5 7.5 10 10.2 9.5 L10 8.2 L8.6 7.8 L8 8.5 C7 8 6 7 5.5 6 L6.2 5.4 L5.8 4 Z" fill="#fff"/></svg>
        <span>+44 (0)203 555 0147</span>
      </li>
      <li>
        <svg class="contact-icon" viewBox="0 0 14 14" aria-hidden="true"><circle cx="7" cy="7" r="7" fill="var(--green)"/><rect x="5" y="3.2" width="4" height="7.6" rx=".8" fill="#fff"/></svg>
        <span>+44 (0)7700 900 318</span>
      </li>
      <li>
        <svg class="contact-icon" viewBox="0 0 14 14" aria-hidden="true"><circle cx="7" cy="7" r="7" fill="var(--green)"/><rect x="3.5" y="4.5" width="7" height="5" fill="#fff"/><path d="M3.5 4.5 L7 7.3 L10.5 4.5" fill="none" stroke="var(--green)" stroke-width=".8"/></svg>
        <span>cmarsh@brightwell-staffing.example</span>
      </li>
      <li>
        <svg class="contact-icon" viewBox="0 0 14 14" aria-hidden="true"><circle cx="7" cy="7" r="7" fill="var(--green)"/><circle cx="7" cy="7" r="3.6" fill="none" stroke="#fff" stroke-width="1"/><path d="M3.4 7 H10.6 M7 3.4 V10.6" stroke="#fff" stroke-width=".8"/></svg>
        <span>www.brightwell-staffing.example</span>
      </li>
    </ul>
  </section>
</body>
</html>
```